Business Card Design (NEW FILES)

ATTENTION: New vector files are available. Please update your design to reflect/use the new (better resolution) logo images.

Seeking a unique and professional business card design for a commercial drone photography/videography business. The layout should feature
the logo (attached) and include the following information:
Owen Tarrick
614-502-7738
www.skylarkreelworks.example
NRD Certified Remote Pilot

Owen Tarrick

```html
<!DOCTYPE html>
<html lang="en">
<head>
<meta charset="utf-8">
<title>Skylark Reelworks – Business Card</title>
<link rel="stylesheet" href="https://fonts.googleapis.com/css2?family=Montserrat:wght@500&family=Open+Sans:wght@400;600;700;800&display=swap">
<style>
  :root {
    --navy: #1c1d4f;
    --orange: #ec8f55;
    --white: #ffffff;
    --stage: #232323;
  }
  * { margin: 0; padding: 0; box-sizing: border-box; }
  html, body { width: 1200px; height: 780px; overflow: hidden; }
  body {
    background: var(--stage);
    font-family: "Open Sans", Arial, sans-serif;
    display: flex;
    align-items: center;
    justify-content: center;
    gap: 50px;
  }
  .card {
    position: relative;
    width: 540px;
    height: 320px;
    background: var(--white);
    border-radius: 24px;
    overflow: hidden;
  }
  .card-bands { position: absolute; inset: 0; width: 100%; height: 100%; }
  .band-navy { fill: var(--navy); }
  .band-orange { fill: var(--orange); }

  /* Wordmark */
  .wordmark {
    position: absolute;
    display: flex;
    align-items: center;
    gap: 10px;
    font-family: "Montserrat", Arial, sans-serif;
    font-weight: 500;
    color: var(--navy);
    letter-spacing: 0.04em;
    text-transform: uppercase;
    line-height: 1.05;
  }
  .wordmark-dot { border-radius: 50%; background: var(--orange); flex: none; }

  .card--front .wordmark { top: 62px; left: 38px; font-size: 22px; }
  .card--front .wordmark-dot { width: 14px; height: 14px; }

  .card--back .wordmark { top: 50%; left: 50%; transform: translate(-50%, -50%); font-size: 40px; }
  .card--back .wordmark-dot { width: 28px; height: 28px; }

  /* Front details */
  .divider { position: absolute; left: 205px; top: 110px; width: 130px; height: 100px; }
  .divider line { stroke: var(--orange); stroke-width: 1.2; }

  .credentials {
    position: absolute;
    left: 40px;
    top: 205px;
    width: 210px;
    text-align: center;
    color: var(--navy);
    font-size: 14px;
    font-weight: 600;
    line-height: 1.4;
  }

  .contact { position: absolute; left: 300px; top: 118px; color: var(--navy); }
  .person-name { font-size: 27px; font-weight: 800; line-height: 1.1; }
  .person-name .first { color: var(--orange); }
  .person-role { font-size: 14px; font-weight: 600; margin-bottom: 14px; }
  .contact-row {
    display: flex; align-items: center; gap: 8px;
    font-size: 13.5px; font-weight: 600; margin-bottom: 6px;
  }
  .contact-icon { width: 13px; height: 13px; flex: none; }
  .contact-icon path, .contact-icon circle { fill: none; stroke: var(--orange); stroke-width: 1.8; }
</style>
</head>
<body>

  <section class="card card--front" aria-label="Business card front">
    <svg class="card-bands" viewBox="0 0 540 320" preserveAspectRatio="none" aria-hidden="true">
      <path class="band-navy" d="M0 0 H300 Q140 8 0 120 Z"/>
      <path class="band-orange" d="M540 320 H200 Q380 300 540 190 Z"/>
    </svg>

    <div class="wordmark"><span class="wordmark-dot"></span><span>Skylark<br>Reelworks</span></div>

    <svg class="divider" viewBox="0 0 130 100" aria-hidden="true">
      <line x1="130" y1="0" x2="0" y2="100"/>
    </svg>

    <p class="credentials">NRD Certified Remote Pilot<br>Fully Insured</p>

    <div class="contact">
      <h1 class="person-name"><span class="first">Owen</span> Tarrick</h1>
      <p class="person-role">Owner</p>
      <p class="contact-row">
        <svg class="contact-icon" viewBox="0 0 16 16" aria-hidden="true"><path d="M4 1.5 L6.5 5 L5 6.5 Q6.5 9.5 9.5 11 L11 9.5 L14.5 12 L12.5 14.5 Q5 13 1.5 3.5 Z"/></svg>
        614-502-7738
      </p>
      <p class="contact-row">
        <svg class="contact-icon" viewBox="0 0 16 16" aria-hidden="true"><circle cx="8" cy="8" r="6.5"/><path d="M1.5 8 H14.5 M8 1.5 Q4 8 8 14.5 M8 1.5 Q12 8 8 14.5"/></svg>
        www.skylarkreelworks.example
      </p>
    </div>
  </section>

  <section class="card card--back" aria-label="Business card back">
    <svg class="card-bands" viewBox="0 0 540 320" preserveAspectRatio="none" aria-hidden="true">
      <path class="band-navy" d="M0 0 H320 Q150 10 0 110 Z"/>
      <path class="band-orange" d="M540 320 H220 Q400 300 540 180 Z"/>
    </svg>
    <div class="wordmark"><span class="wordmark-dot"></span><span>Skylark<br>Reelworks</span></div>
  </section>

</body>
</html>
```